Brimsett Gardening Fresh New Website

We are looking to create a simple fresh website for our landscaping business. The website should appeal to a 'high end' audience. We deal with a lot of Embassies and affluent clients who have extremely large gardens that are meticulously maintained. The site is about communicating our excellent landscaping and customer service skills and encouraging new clients to reach out and engage us to take care of their gardens.

The website is basically going to be our business card, it will have almost no functionality other than two 'contact us' forms, one for smaller clients and one for more detailed projects.

The website will not have a lot of written content and will have to show photos of beautifully landscaped gardens.

The main logo in black will influence the site, however, we are open to all suggestions.

We are expecting to have the following pages:
Home Page
Services
About Us
Contact Us
Showcase (photo gallery of our work)

We need someone who can code it to wordpress and be available for minor changes over a number of days. They will be simple tweaks.

```html
<!DOCTYPE html>
<html lang="en">
<head>
<meta charset="utf-8">
<title>Brimsett Gardening</title>
<link rel="stylesheet" href="https://fonts.googleapis.com/css2?family=Cinzel:wght@400;500&family=Poppins:wght@300;400;500;600&display=swap">
<style>
:root{
  --dark:#1e1a17;
  --gold:#d9a93c;
  --white:#ffffff;
  --ink:#1f1f1f;
  --muted:#555555;
  --rule:#4a4541;
}
*{margin:0;padding:0;box-sizing:border-box}
html,body{width:1200px;height:4448px;overflow:hidden}
body{position:relative;background:var(--white);font-family:'Poppins',sans-serif;color:var(--ink)}
.abs{position:absolute}
.serif{font-family:'Cinzel',serif;font-weight:400}
.photo{position:absolute}

/* header */
.site-header{position:absolute;left:0;top:0;width:1200px;height:112px;background:var(--dark);z-index:2}
.nav-link{position:absolute;top:36px;font-size:18px;color:var(--white);letter-spacing:.3px}
.nav-cta{position:absolute;left:934px;top:22px;width:150px;height:56px;border:2px solid var(--gold);color:var(--gold);font-size:18px;display:flex;align-items:center;justify-content:center;font-weight:500}
.logo-tab{position:absolute;left:485px;top:0;width:230px;height:164px;background:var(--dark);border-radius:0 0 115px 115px / 0 0 50px 50px;z-index:3}
.logo-dot{position:absolute;left:97px;top:12px;width:36px;height:36px;border:2px solid var(--gold);border-radius:50%}
.brand-name{position:absolute;left:0;width:100%;text-align:center;font-family:'Poppins',sans-serif;font-weight:500;color:var(--gold);letter-spacing:0}
.logo-tab .brand-name{top:96px;font-size:20px;line-height:28px}

/* hero */
.hero{position:absolute;left:0;top:112px;width:1200px;height:620px;background:linear-gradient(120deg,#2e4a1c 0%,#5c7a2c 35%,#6e8a34 55%,#3b5220 80%,#2a3a1a 100%)}
.hero-title{position:absolute;left:112px;top:96px;font-size:62px;line-height:69px;color:var(--white)}
.hero-text{position:absolute;left:112px;top:254px;width:430px;font-size:19px;line-height:30px;color:var(--white)}
.btn-light{position:absolute;background:var(--white);color:var(--ink);font-size:19px;display:flex;align-items:center;justify-content:center}
.btn-dark{position:absolute;background:var(--dark);color:var(--gold);font-size:18px;display:flex;align-items:center;justify-content:center}

/* welcome */
.welcome{position:absolute;left:0;top:732px;width:1200px;height:497px;background:linear-gradient(180deg,#e3ead9 0%,#f1f3ec 45%,#e8e6df 100%)}
.section-title{font-size:40px;line-height:46px;color:var(--ink)}
.welcome-text{position:absolute;left:509px;top:190px;width:585px;font-size:16px;line-height:28.5px;color:var(--muted)}

/* services */
.service-photo{position:absolute;top:1392px;width:311px;height:312px;border-radius:70px 0 70px 0}
.service-label{position:absolute;top:1724px;width:311px;text-align:center;font-size:22px;color:var(--ink)}

/* why */
.why{position:absolute;left:0;top:1835px;width:1200px;height:575px;background:linear-gradient(115deg,#2f5a22 0%,#3f7a27 40%,#d8d8d2 62%,#c8cbbd 78%,#5b7d32 100%)}
.why-list{position:absolute;left:112px;top:268px;list-style:none}
.why-list li{display:flex;align-items:center;height:52px;font-size:22px;color:var(--white)}
.why-list svg{margin-right:14px}

/* call to action */
.cta{position:absolute;left:0;top:3717px;width:1200px;height:335px;background:linear-gradient(160deg,#2f4a1a 0%,#3a6a22 45%,#56922e 70%,#2c3d1a 100%)}
.cta-title{position:absolute;left:0;top:64px;width:1200px;text-align:center;font-size:38px;line-height:52px;font-weight:600;color:var(--white)}

/* footer */
.site-footer{position:absolute;left:0;top:4052px;width:1200px;height:396px;background:var(--dark);color:var(--white)}
.footer-mark{position:absolute;left:208px;top:60px;width:56px;height:56px;border:2px solid var(--gold);border-radius:50%}
.footer-brand{position:absolute;left:86px;top:170px;width:300px}
.footer-brand .brand-name{top:0;font-size:28px;line-height:36px}
.footer-heading{position:absolute;top:58px;font-size:20px;font-weight:500}
.footer-links{position:absolute;left:482px;top:105px;list-style:none}
.footer-links li{height:35px;font-size:16px}
.contact-row{position:absolute;left:682px;display:flex;align-items:flex-start;font-size:16px;line-height:28px}
.contact-row svg{margin-right:10px;margin-top:6px;flex:none}
.footer-rule{position:absolute;left:112px;top:308px;width:976px;height:1px;background:var(--rule)}
.copyright{position:absolute;left:112px;top:336px;font-size:16px}
.social{position:absolute;top:326px;width:44px;height:44px;border:1.5px solid var(--gold);border-radius:50%}
</style>
</head>
<body>

<header class="site-header">
  <span class="nav-link" style="left:112px">HOME</span>
  <span class="nav-link" style="left:202px">ABOUT US</span>
  <span class="nav-link" style="left:328px">SERVICES</span>
  <span class="nav-link" style="left:770px">SHOWCASE</span>
  <span class="nav-cta">CONTACT US</span>
</header>
<div class="logo-tab">
  <span class="logo-dot"></span>
  <span class="brand-name">Brimsett Gardening</span>
</div>

<section class="hero" role="img" aria-label="Landscaped garden border with lit bollard lights, shrubs and curving stone edging">
  <h1 class="hero-title serif">BRIMSETT<br>GARDENING</h1>
  <p class="hero-text">We deal with a lot of Embassies and affluent clients who have extremely large gardens that are meticulously maintained.</p>
  <span class="btn-light" style="left:112px;top:387px;width:245px;height:69px">CONTACT US TODAY</span>
</section>

<section class="welcome" role="img" aria-label="Soft faded view of a lawn edged with pebbles">
  <h2 class="section-title serif abs" style="left:509px;top:68px">WELCOME TO<br>BRIMSETT GARDENING</h2>
  <p class="welcome-text">Lorem ipsum dolor sit amet, consectetur adipiscing elit, sed do eiusmod tempor incididunt ut labore et dolore magna aliqua. Ut enim ad minim veniam, quis nostrud exercitation ullamco laboris nisi ut aliquip ex ease commodo consequat. Duis aute irure dolor in reprehenderit in voluptate velit esse cillum dolore eu fugiat nulla pariatur.</p>
  <span class="btn-dark" style="left:509px;top:364px;width:151px;height:56px">READ MORE</span>
</section>

<h2 class="section-title serif abs" style="left:0;top:1308px;width:1200px;text-align:center">OUR SERVICES</h2>
<div class="service-photo" style="left:112px;background:linear-gradient(150deg,#8a5a3a,#3f8a22 55%,#2f6a1a)" role="img" aria-label="Lawn mower cutting fresh grass"></div>
<div class="service-photo" style="left:444px;background:linear-gradient(160deg,#3a2e28 0%,#d8dcd4 35%,#a9cfb8 70%,#6fb07a)" role="img" aria-label="Hand drawing a coloured landscape design plan"></div>
<div class="service-photo" style="left:777px;background:linear-gradient(170deg,#6a8a4a 0%,#4a6a2e 40%,#8a7a66 60%,#4a9a2a 100%)" role="img" aria-label="Gardener rolling out new turf"></div>
<span class="service-label" style="left:112px">Maintenance</span>
<span class="service-label" style="left:444px">Landscape Design Plans</span>
<span class="service-label" style="left:777px">Restoration</span>

<section class="why" role="img" aria-label="Lawn beside a bed of white pebbles with shrubs and a garden light">
  <h2 class="section-title serif abs" style="left:112px;top:72px;color:var(--white)">WHY CHOOSE<br>BRIMSETT GARDENING</h2>
  <p class="abs" style="left:112px;top:182px;width:470px;font-size:16px;line-height:28px;color:var(--white)">Ut enim ad minim veniam, quis nostrud exercitation ull amco laboris nisi ut aliquip ex ease .</p>
  <ul class="why-list">
    <li><svg width="22" height="22" viewBox="0 0 22 22"><circle cx="11" cy="11" r="10" fill="none" stroke="#fff" stroke-width="1.5"/><path d="M6 11.5l3.3 3.3L16 8" fill="none" stroke="#fff" stroke-width="1.8"/></svg>Excellent landscaping</li>
    <li><svg width="22" height="22" viewBox="0 0 22 22"><circle cx="11" cy="11" r="10" fill="none" stroke="#fff" stroke-width="1.5"/><path d="M6 11.5l3.3 3.3L16 8" fill="none" stroke="#fff" stroke-width="1.8"/></svg>Customer service skills</li>
    <li><svg width="22" height="22" viewBox="0 0 22 22"><circle cx="11" cy="11" r="10" fill="none" stroke="#fff" stroke-width="1.5"/><path d="M6 11.5l3.3 3.3L16 8" fill="none" stroke="#fff" stroke-width="1.8"/></svg>Professional Team</li>
    <li><svg width="22" height="22" viewBox="0 0 22 22"><circle cx="11" cy="11" r="10" fill="none" stroke="#fff" stroke-width="1.5"/><path d="M6 11.5l3.3 3.3L16 8" fill="none" stroke="#fff" stroke-width="1.8"/></svg>Unique and Reliability</li>
  </ul>
</section>

<h2 class="section-title serif abs" style="left:0;top:2486px;width:1200px;text-align:center">SHOWCASE</h2>
<div class="photo" style="left:112px;top:2567px;width:478px;height:342px;background:linear-gradient(160deg,#5a5a3a,#3f8a22 50%,#b8a8a0 90%)" role="img" aria-label="Curving paved path through a green lawn and planted beds"></div>
<div class="photo" style="left:608px;top:2567px;width:480px;height:342px;background:linear-gradient(180deg,#e8e8e8 0%,#4f9a2a 30%,#a8a8a4 60%,#c8c8c4)" role="img" aria-label="Stone steps between lawn terraces with a potted plant"></div>
<div class="photo" style="left:112px;top:2925px;width:314px;height:295px;background:linear-gradient(120deg,#8a8a86,#9a9a94 40%,#3f8a22 60%,#2f7a1a)" role="img" aria-label="Clipped shrub balls beside stone steps"></div>
<div class="photo" style="left:442px;top:2925px;width:314px;height:295px;background:linear-gradient(180deg,#1a2a1a,#2f4a22 50%,#8a5a44)" role="img" aria-label="Lit stone garden path at night"></div>
<div class="photo" style="left:773px;top:2925px;width:315px;height:295px;background:linear-gradient(180deg,#3a7ad0 0%,#9a8878 45%,#4a8a2a 70%,#a07868)" role="img" aria-label="Large house with a circular planted driveway bed"></div>
<div class="photo" style="left:112px;top:3236px;width:314px;height:295px;background:linear-gradient(180deg,#6aa0d8 0%,#4a7a2e 35%,#b08a6a 70%,#a07a5a)" role="img" aria-label="Paved driveway curving towards a house"></div>
<div class="photo" style="left:442px;top:3236px;width:314px;height:295px;background:linear-gradient(180deg,#4a6a2e 0%,#8a8a7a 40%,#5aa030 70%,#4a8a22)" role="img" aria-label="Stone bridge over a lawn in a park garden"></div>
<div class="photo" style="left:773px;top:3236px;width:315px;height:295px;background:linear-gradient(180deg,#4a7a2a 0%,#b08a6a 40%,#6a6a6a 75%,#5a5a58)" role="img" aria-label="Backyard patio with lit stone fire pit and timber fence"></div>
<span class="btn-dark" style="left:525px;top:3583px;width:150px;height:55px">VIEW MORE</span>

<section class="cta" role="img" aria-label="Freshly laid lawn beside a dark soil garden bed">
  <h2 class="cta-title">Save Time &amp; Money – Get It started<br>with Brimsett Gardening</h2>
  <span class="btn-light" style="left:521px;top:197px;width:159px;height:59px;font-size:18px">CONTACT US</span>
</section>

<footer class="site-footer">
  <div class="footer-mark"></div>
  <div class="footer-brand">
    <span class="brand-name">Brimsett Gardening</span>
  </div>
  <span class="footer-heading" style="left:482px">Quick links</span>
  <ul class="footer-links">
    <li>Home</li><li>About Us</li><li>Services</li><li>Showcase</li><li>Contact Us</li>
  </ul>
  <span class="footer-heading" style="left:682px">Contact Us</span>
  <div class="contact-row" style="top:106px">
    <svg width="12" height="16" viewBox="0 0 12 16"><path d="M6 0a6 6 0 0 0-6 6c0 4.5 6 10 6 10s6-5.5 6-10a6 6 0 0 0-6-6zm0 8.5A2.5 2.5 0 1 1 6 3.5a2.5 2.5 0 0 1 0 5z" fill="var(--gold)"/></svg>
    <span>No 1234 emo enimam volupta<br>tem quia voluptas</span>
  </div>
  <div class="contact-row" style="top:190px">
    <svg width="14" height="14" viewBox="0 0 14 14"><path d="M3 0l2.5 3.5-1.5 1.8c.8 1.8 2.3 3.3 4.2 4.2l1.8-1.5L14 10.5 12 14C5.5 13.5.5 8.5 0 2z" fill="var(--gold)"/></svg>
    <span>1 800 555 0142</span>
  </div>
  <div class="contact-row" style="top:245px">
    <svg width="16" height="12" viewBox="0 0 16 12"><rect width="16" height="12" rx="1.5" fill="var(--gold)"/><path d="M1 1.5l7 5 7-5" fill="none" stroke="var(--dark)" stroke-width="1.4"/></svg>
    <span>info@brimsettgardening.au</span>
  </div>
  <div class="footer-rule"></div>
  <span class="copyright">© 2024, Brimsett Gardening | All Rights Reserved.</span>
  <span class="social" style="left:941px"></span>
  <span class="social" style="left:993px"></span>
  <span class="social" style="left:1045px"></span>
</footer>

</body>
</html>
```